Trade Show Design

Two, doublesided backdrops/one doublesided banner/one countertop. I have 3 sample pictures of the 3 items that we are purchasing and all the dimensions are listed on the file names.
website: www.brickwisestudio.net
We are a training center that teaches homeowner's how to do their own home renovations through in-person classes with hands-on training.
We are looking to update our tradeshow displays utilizing stock photos as our photos do not have high enough resolution. I have attached lots of example pictures to select from but some of my favourites that I want to use are over 10 MB so they won't upload. Will have to figure out a different way to upload. Our tagline is tackle any project like a pro. We also use words such as "learn to reno" or "practical, hands-on training". We want to use our current branding (pictures of our minivan are uploaded as well) and our color palette document and really show people what we are all about - classes that people can attend so they can learn to reno their home.
Updates

For the 2 backdrops, we would like them to either be stand-alone or together incase we go to a trade show and only have room for 1 of them. They are to be different designs, front and back but a continuous flow if we are to use them together. Again, I have to figure out how to upload additional pictures as some of the ones I want to use are larger. Thanks!

Same with the Banner that is also double-sided - this is to be a different design for the back and front. We want minimal wording on everything but we really want to showcase what we do so that people can figure it out quickly when they walk by our booth....we offer in-person class with hands-on training. Learn to do by doing. Like on our vehicle that I sent example pictures of, we can put a list of a few topics so that people can understand:
Renovation Topics:
Bathroom
Drywall
Flooring
Tiling
Basement
Framing
Plumbing
Baseboards
Feature Walls

Here is the link to the Vornel Box to additional photos.

https://files.vornelbox.net/shared/7QK4r_mz2-TX8LwBnPe5YuJsdA0fGhRkZ?view=open

Thanks,
Marla

```html
<!DOCTYPE html>
<html lang="en">
<head>
<meta charset="utf-8">
<title>Brickwise Studio – Trade Show Backdrops</title>
<link href="https://fonts.googleapis.com/css2?family=Anton&family=Poppins:wght@400;600&display=swap" rel="stylesheet">
<style>
  :root{
    --bg:#dfe5ec;
    --teal:#2b6f79;
    --teal-dark:#1f5f6a;
    --cream:#e8e6b4;
    --sage:#d4d3a0;
    --stone:#9b9a88;
    --sky:#b8d4ef;
    --orange:#e9a53b;
    --gold:#f2b92c;
    --white:#ffffff;
  }
  *{box-sizing:border-box;margin:0;padding:0}
  html,body{width:1200px;height:900px;overflow:hidden;background:var(--bg)}
  body{position:relative;font-family:"Poppins",sans-serif}

  .backdrop{position:absolute;top:216px;width:560px;height:467px;overflow:hidden;background:var(--cream)}
  .backdrop--reno{left:30px}
  .backdrop--training{left:610px}

  .tile{position:absolute;display:flex;flex-direction:column;align-items:center;justify-content:center;text-align:center}
  .photo{position:absolute}

  .tile--cream{background:var(--cream)}
  .tile--teal{background:var(--teal)}
  .tile--stone{background:var(--stone)}
  .tile--sky{background:var(--sky)}

  .topics{font-weight:600;font-size:11px;line-height:1.45;text-transform:uppercase;letter-spacing:.01em}
  .topics--light{color:var(--white)}
  .topics--dark{color:var(--teal-dark)}
  .topic-icon{width:34px;height:34px;margin-bottom:14px}

  .brand{display:flex;flex-direction:column;align-items:center;gap:5px}
  .brand-row{display:flex;align-items:center;gap:5px;white-space:nowrap}
  .brand-mark{width:11px;height:11px;background:var(--gold);flex:none}
  .brand-name{font-weight:600;font-size:13px;color:var(--teal-dark);letter-spacing:.01em}
  .brand-tagline{font-weight:400;font-size:7.5px;color:var(--teal-dark);white-space:nowrap}

  .headline{font-family:"Anton",sans-serif;color:var(--white);font-size:50px;line-height:1.02;letter-spacing:-.01em}
  .swoosh{width:110px;height:16px;margin-top:2px}

  .url-pill{display:flex;align-items:center;background:var(--teal-dark);border-radius:4px;height:24px;padding:0 10px 0 0;color:var(--white);font-size:9px;font-weight:400;white-space:nowrap}
  .url-dot{width:26px;height:26px;border-radius:50%;background:var(--gold);display:flex;align-items:center;justify-content:center;margin:0 8px 0 -4px}
  .url-dot svg{width:10px;height:10px}

  .practical{position:absolute;left:0;top:0;width:224px;height:467px;background:linear-gradient(160deg,#d7d69f 0%,#c4c48c 55%,#b9ba84 100%)}
  .practical .brand{position:absolute;left:0;right:0;top:66px}
  .practical-head{position:absolute;left:14px;top:170px;font-family:"Anton",sans-serif;color:var(--teal-dark);font-size:38px;line-height:1.12}
  .hands-on{display:inline-block;background:var(--stone);color:var(--white);padding:0 10px;transform:rotate(-2deg);margin:2px 0}
  .practical-swoosh{position:absolute;left:34px;top:322px;width:90px;height:12px}
  .practical .url-pill{position:absolute;left:30px;top:404px}
</style>
</head>
<body>

<section class="backdrop backdrop--reno" aria-label="Learn to Reno backdrop">
  <div class="photo" role="img" aria-label="Woman measuring a wood board in a workshop" style="left:0;top:0;width:145px;height:161px;background:linear-gradient(135deg,#6d5645,#b69a7c 60%,#8fa6b8)"></div>
  <div class="tile tile--cream" style="left:145px;top:0;width:145px;height:161px">
    <div class="brand">
      <div class="brand-row"><span class="brand-mark"></span><span class="brand-name">Brickwise Studio</span></div>
      <span class="brand-tagline">Take on any job with real skill.</span>
    </div>
  </div>
  <div class="photo" role="img" aria-label="Smiling woman holding a hammer" style="left:290px;top:0;width:145px;height:161px;background:linear-gradient(150deg,#c8c0b4,#7d8fa8 55%,#3a3a3e)"></div>
  <div class="tile tile--stone" style="left:435px;top:0;width:125px;height:161px">
    <svg class="topic-icon" viewBox="0 0 34 34" aria-hidden="true"><rect x="6" y="6" width="18" height="9" rx="2" fill="#fff"/><rect x="24" y="9" width="8" height="3" fill="#fff"/><rect x="10" y="15" width="7" height="11" fill="#fff"/><rect x="8" y="26" width="11" height="6" rx="1" fill="#fff"/></svg>
    <p class="topics topics--light">Drywall<br>Feature Walls<br>Framing</p>
  </div>

  <div class="tile tile--cream" style="left:0;top:161px;width:145px;height:162px">
    <svg class="topic-icon" viewBox="0 0 34 34" aria-hidden="true"><path d="M6 32V10a6 6 0 0 1 12 0" fill="none" stroke="#1f5f6a" stroke-width="3"/><path d="M12 12a10 10 0 0 1 14 6z" fill="#1f5f6a"/><g stroke="#1f5f6a" stroke-width="1.6" stroke-dasharray="2 2"><line x1="17" y1="20" x2="15" y2="30"/><line x1="21" y1="20" x2="21" y2="30"/><line x1="25" y1="20" x2="27" y2="30"/></g></svg>
    <p class="topics topics--dark">Tiling<br>Bathroom<br>Plumbing</p>
  </div>
  <div class="tile tile--teal" style="left:145px;top:161px;width:290px;height:162px">
    <h1 class="headline">Learn<br>To Reno</h1>
    <svg class="swoosh" viewBox="0 0 110 16" aria-hidden="true"><path d="M2 9 Q50 4 108 6 M58 14 Q80 8 106 9" fill="none" stroke="var(--orange)" stroke-width="2" stroke-linecap="round"/></svg>
  </div>
  <div class="tile tile--sky" style="left:435px;top:161px;width:125px;height:162px">
    <svg class="topic-icon" viewBox="0 0 34 34" aria-hidden="true"><rect x="3" y="16" width="28" height="16" fill="#1f5f6a"/><rect x="8" y="4" width="4" height="14" fill="#1f5f6a"/><rect x="20" y="6" width="4" height="12" fill="#1f5f6a"/><rect x="9" y="24" width="16" height="3" fill="#b8d4ef"/></svg>
    <p class="topics topics--dark">Flooring<br>Baseboards<br>Basement</p>
  </div>

  <div class="photo" role="img" aria-label="Couple renovating a room with a paint roller" style="left:0;top:323px;width:196px;height:144px;background:linear-gradient(120deg,#e9e6e1,#b9a9c9 45%,#3d4a66)"></div>
  <div class="tile tile--cream" style="left:196px;top:323px;width:172px;height:144px">
    <div class="url-pill"><span class="url-dot"><svg viewBox="0 0 10 10"><path d="M2 1 L8 5.5 L5 6 L4 9 Z" fill="#1f5f6a"/></svg></span>brickwisestudio.net</div>
  </div>
  <div class="photo" role="img" aria-label="Woman in safety glasses using a power drill" style="left:368px;top:323px;width:192px;height:144px;background:linear-gradient(140deg,#8a8f98,#a48466 50%,#5b4a3e)"></div>
</section>

<section class="backdrop backdrop--training" aria-label="Practical Hands-on Training backdrop">
  <div class="practical" role="img" aria-label="Faded photo of a person working with tools, tinted sage">
    <div class="brand">
      <div class="brand-row"><span class="brand-mark"></span><span class="brand-name">Brickwise Studio</span></div>
      <span class="brand-tagline">Take on any job with real skill.</span>
    </div>
    <h2 class="practical-head">Practical,<br><span class="hands-on">Hands-on</span><br>Training.</h2>
    <svg class="practical-swoosh" viewBox="0 0 90 12" aria-hidden="true"><path d="M2 6 Q45 3 88 5" fill="none" stroke="var(--orange)" stroke-width="2" stroke-linecap="round"/></svg>
    <div class="url-pill"><span class="url-dot"><svg viewBox="0 0 10 10"><path d="M2 1 L8 5.5 L5 6 L4 9 Z" fill="#1f5f6a"/></svg></span>brickwisestudio.net</div>
  </div>

  <div class="tile tile--teal" style="left:224px;top:0;width:177px;height:162px">
    <svg class="topic-icon" viewBox="0 0 34 34" aria-hidden="true"><rect x="6" y="6" width="18" height="9" rx="2" fill="#fff"/><rect x="24" y="9" width="8" height="3" fill="#fff"/><rect x="10" y="15" width="7" height="11" fill="#fff"/><rect x="8" y="26" width="11" height="6" rx="1" fill="#fff"/></svg>
    <p class="topics topics--light">Drywall<br>Feature Walls<br>Framing</p>
  </div>
  <div class="tile tile--cream" style="left:401px;top:0;width:159px;height:162px">
    <svg class="topic-icon" viewBox="0 0 34 34" aria-hidden="true"><rect x="3" y="16" width="28" height="16" fill="#1f5f6a"/><rect x="8" y="4" width="4" height="14" fill="#1f5f6a"/><rect x="20" y="6" width="4" height="12" fill="#1f5f6a"/><rect x="9" y="24" width="16" height="3" fill="#e8e6b4"/></svg>
    <p class="topics topics--dark">Flooring<br>Baseboards<br>Basement</p>
  </div>

  <div class="photo" role="img" aria-label="Two people installing a ceiling light fixture" style="left:224px;top:162px;width:336px;height:156px;background:linear-gradient(130deg,#f1eeea,#d9d2cb 45%,#b6504a 80%,#8c7a6c)"></div>

  <div class="photo" role="img" aria-label="Couple sitting on the floor with a toolbox" style="left:224px;top:318px;width:177px;height:149px;background:linear-gradient(140deg,#c9b8a0,#8b3b3a 55%,#4a3d36)"></div>
  <div class="tile tile--sky" style="left:401px;top:318px;width:159px;height:149px">
    <svg class="topic-icon" viewBox="0 0 34 34" aria-hidden="true"><path d="M6 32V10a6 6 0 0 1 12 0" fill="none" stroke="#1f5f6a" stroke-width="3"/><path d="M12 12a10 10 0 0 1 14 6z" fill="#1f5f6a"/><g stroke="#1f5f6a" stroke-width="1.6" stroke-dasharray="2 2"><line x1="17" y1="20" x2="15" y2="30"/><line x1="21" y1="20" x2="21" y2="30"/><line x1="25" y1="20" x2="27" y2="30"/></g></svg>
    <p class="topics topics--dark">Tiling<br>Bathroom<br>Plumbing</p>
  </div>
</section>

</body>
</html>
```